Buch-/eBook-Cover für Krimi
Er hat genau die Vorgaben umgesetzt und sich mit mir sehr kooperativ ausgetauscht
Zielgruppe
Krimileser
Aufgabenstellung
Auf dem Cover muss stehen:
Harald Bruck
Die Spur der gläsernen Reiter
Ein Fall für den bayerischen Barnaby Quince
Wie der Untertitel sagt, habe ich eine Reihe um den Franz Kiefer gestartet, der eine Art bayerischer Barnaby Quince ist. Er hat eine kalte Meerschaumpfeife im Mund, weil er sich das Rauchen abgewöhnt, und trägt bayerische Tracht inkl. Hut. Sein Sidekick ist allerdings Frau Dr. Brunner. Die Pilbury-Figur, aus deren Sicht die Geschichte erzählt wird, ist also eine Frau. Die weißen Soldaten sind Auomaten aus dem 19. Jahrhundert, die Marschmusik spielen und der Schlüssel zu einem spektakulären Schatz sind. Dass es sich um Automaten handelt, sollte natürlich nicht im Cover vorweggenommen werden. Stilisierte weiße Soldaten aus dem 18. oder 19. Jahrhundert kann man aber durchaus einbringen. Prinzipiell hätte ich gerne eine Reminiszenz an den klassischen Barnaby Quince in bayerischem Gewand und zeitgenössisch. Der Roman spielt im Jahr 2023

```html
<!DOCTYPE html>
<html lang="de">
<head>
<meta charset="utf-8">
<title>Die Spur der gläsernen Reiter – Cover</title>
<link rel="stylesheet" href="https://fonts.googleapis.com/css2?family=Anton&family=Montserrat:wght@700&display=swap">
<style>
  :root {
    --stage: #dfe3e7;
    --cover-black: #110e0d;
    --glow-core: #fff2b8;
    --glow-mid: #f0a02c;
    --glow-outer: #7a4513;
    --glow-edge: #2a1a0e;
    --accent-orange: #ea7a22;
    --text-white: #f4f4f2;
  }
  html, body {
    margin: 0;
    width: 1200px;
    height: 1117px;
    overflow: hidden;
    background: var(--stage);
  }
  .cover {
    position: absolute;
    left: 244px;
    top: 50px;
    width: 712px;
    height: 1017px;
    background: var(--cover-black);
    overflow: hidden;
    box-shadow: 0 18px 40px rgba(0,0,0,0.25);
  }
  .cover-art {
    position: absolute;
    inset: 0 0 auto 0;
    height: 600px;
    background:
      radial-gradient(ellipse 230px 230px at 50% 46%, var(--glow-core) 0%, #ffd25a 22%, var(--glow-mid) 48%, var(--glow-outer) 75%, transparent 100%),
      linear-gradient(180deg, var(--glow-edge) 0%, #5a3414 40%, #3a2410 75%, var(--cover-black) 100%);
  }
  .author {
    position: absolute;
    top: 68px;
    left: 0;
    right: 0;
    text-align: center;
    font-family: "Anton", sans-serif;
    font-size: 34px;
    letter-spacing: 22px;
    color: var(--text-white);
    padding-left: 22px;
  }
  .author .star { color: var(--text-white); letter-spacing: 22px; }
  .title {
    position: absolute;
    top: 560px;
    left: 0;
    right: 0;
    margin: 0;
    text-align: center;
    font-family: "Anton", sans-serif;
    font-weight: 400;
    text-transform: uppercase;
    line-height: 1;
  }
  .title-line { display: block; position: relative; }
  .title-line--lead { font-size: 84px; color: var(--text-white); }
  .title-line--middle { font-size: 62px; color: var(--text-white); margin-top: 8px; }
  .title-line--key { font-size: 128px; color: var(--accent-orange); margin-top: 6px; }
  .rule {
    position: absolute;
    height: 4px;
    background: var(--accent-orange);
  }
  .rule--left { left: 36px; top: 656px; width: 130px; }
  .rule--right { right: 36px; top: 748px; width: 130px; }
  .subtitle {
    position: absolute;
    top: 900px;
    left: 0;
    right: 0;
    margin: 0;
    text-align: center;
    font-family: "Montserrat", sans-serif;
    font-weight: 700;
    font-size: 27px;
    line-height: 1.2;
    color: var(--text-white);
    text-transform: uppercase;
  }
</style>
</head>
<body>
  <div class="cover">
    <div class="cover-art" role="img" aria-label="Silhouette eines Soldaten mit Gewehr vor einem glühenden orangefarbenen Lichtschein"></div>
    <div class="author">HARALD <span class="star">★</span>BRUCK</div>
    <span class="rule rule--left"></span>
    <span class="rule rule--right"></span>
    <h1 class="title">
      <span class="title-line title-line--lead">Die Spur</span>
      <span class="title-line title-line--middle">der gläsernen</span>
      <span class="title-line title-line--key">Reiter</span>
    </h1>
    <p class="subtitle">Ein Fall für den bayerischen<br>Barnaby Quince</p>
  </div>
</body>
</html>
```